Home Security Company Business Card

Looking for a eye catching business card that is non traditional and stands out but yet still looks professional. It should include all the pertinent information such as name, title, address, telephone, e-mail, website address should definitely stand out and then finally the logo.

Target Market(s)

Residential and Commercial accounts mostly upscale accounts

Industry/Entity Type

Security

Contact Information for Business Card

Name
Title
Address
Office #
Cell #
E-mail
Website

Font styles to use
Serif
Sans Serif

Requirements
Must have
• Logo, two sided color configuration
Nice to have
• You decide
Should not have
• There really aren't any.

```html
<!DOCTYPE html>
<html lang="en">
<head>
<meta charset="utf-8">
<title>Ironvale Protection Group – Business Card</title>
<link rel="stylesheet" href="https://fonts.googleapis.com/css2?family=Arimo:wght@400;700&display=swap">
<style>
  :root {
    --stage: #2f2926;
    --card: #1c1c1d;
    --card-edge: #262627;
    --brand-red: #8e1a12;
    --accent-gold: #d69a1e;
    --text-light: #e6e6e6;
    --icon-red: #9a1c14;
  }
  * { box-sizing: border-box; margin: 0; padding: 0; }
  html, body {
    width: 1200px; height: 787px; overflow: hidden;
    background: var(--stage);
    font-family: "Arimo", Arial, sans-serif;
  }
  .stage {
    width: 1200px; height: 787px;
    display: flex; align-items: center; justify-content: center; gap: 50px;
  }
  .card {
    position: relative;
    width: 540px; height: 309px;
    background: var(--card);
    border: 1px solid var(--card-edge);
    box-shadow: 0 10px 30px rgba(0,0,0,.45);
  }
  .brand {
    display: flex; align-items: center; gap: 12px;
    color: var(--brand-red);
    font-weight: 700; font-size: 26px; letter-spacing: .5px;
    text-transform: uppercase;
  }
  .brand-mark {
    width: 14px; height: 14px; border-radius: 50%;
    background: var(--brand-red);
  }
  /* front side */
  .card-front .brand {
    position: absolute; left: 0; right: 0; top: 112px; justify-content: center;
  }
  .card-front .site {
    position: absolute; left: 0; right: 0; top: 200px; text-align: center;
    color: var(--text-light); font-size: 13px; letter-spacing: 3px;
  }
  /* back side */
  .card-back .brand {
    position: absolute; left: 210px; top: 70px; font-size: 22px;
  }
  .holder { position: absolute; left: 36px; top: 142px; }
  .holder-name { color: var(--brand-red); font-size: 17px; }
  .holder-title { color: var(--accent-gold); font-size: 14px; margin-top: 4px; }
  .holder-address { color: var(--text-light); font-size: 14px; line-height: 1.45; margin-top: 8px; }
  .contacts {
    position: absolute; right: 24px; bottom: 22px;
    list-style: none; text-align: right;
  }
  .contacts li {
    display: flex; align-items: center; justify-content: flex-end; gap: 12px;
    color: var(--text-light); font-size: 14px; line-height: 24px;
  }
  .contacts svg { width: 14px; height: 14px; fill: var(--icon-red); }
</style>
</head>
<body>
<main class="stage">
  <section class="card card-front">
    <div class="brand"><span class="brand-mark"></span>Ironvale Protection Group</div>
    <p class="site">www.ironvale.com</p>
  </section>

  <section class="card card-back">
    <div class="brand"><span class="brand-mark"></span>Ironvale Protection Group</div>
    <div class="holder">
      <p class="holder-name">Marcus Hale</p>
      <p class="holder-title">President</p>
      <p class="holder-address">2719 Alderbrook Lane<br>Cedar Hollow, NY 11590</p>
    </div>
    <ul class="contacts">
      <li>555 8143 2096
        <svg viewBox="0 0 16 16" aria-hidden="true"><path d="M3 6c0-2 2-3 5-3s5 1 5 3l-2 1-1-2H6L5 7 3 6zm1 3h8l1 5H3l1-5zm4 1a1.5 1.5 0 100 3 1.5 1.5 0 000-3z"/></svg></li>
      <li>555 3720 6418
        <svg viewBox="0 0 16 16" aria-hidden="true"><path d="M5 1h6a1 1 0 011 1v12a1 1 0 01-1 1H5a1 1 0 01-1-1V2a1 1 0 011-1zm0 2v9h6V3H5zm3 10a.8.8 0 100 1.6A.8.8 0 008 13z"/></svg></li>
      <li>marcus@ironvale.com
        <svg viewBox="0 0 16 16" aria-hidden="true"><path d="M1 4h14v9H1V4zm1 1v.3l6 4 6-4V5H2z"/></svg></li>
      <li>www.ironvale.com
        <svg viewBox="0 0 16 16" aria-hidden="true"><circle cx="8" cy="8" r="7"/><path d="M1 8h14M8 1c3 3 3 11 0 14M8 1c-3 3-3 11 0 14" stroke="#1c1c1d" stroke-width="1" fill="none"/></svg></li>
    </ul>
  </section>
</main>
</body>
</html>
```